Hybrid Seed corn and Soybean Sales business needs a website.

We here at "KW Grain" feel that we need a website to show a very professional side to our customer base. Although no actual ordering will take place on this website, we would like to put Plot and field trail data on the website. Along with a brief page for each of our hybrids and a place for customers to sign up for a newsletter. The company we sell hybrids for is MolvanGrain.com... Im not sure how this process works as far as myself updating the information or having the data actually put on the website, but feel free to contact me if you need the information. I will attach the logo for the company, (KW Grain).

Target Market(s)

Farmers, "Producers", Corn and soybean production

Industry/Entity Type

Business

Coding

Coded - Design and coding required

Number of Pages Required

5+ page

Colors
f78f20
ffffff

Requirements
Nice to have
• Similar layout to http://www.molvangrain.com/
• And it would be nice to incorporate our story into the website
• http://www.molvangrain.com/our-story/molvan-today/

```html
<!DOCTYPE html>
<html lang="en">
<head>
<meta charset="utf-8">
<title>KW Grain</title>
<link rel="stylesheet" href="https://fonts.googleapis.com/css2?family=PT+Serif:wght@400;700&display=swap">
<style>
:root{
  --orange:#f78f20;
  --orange-dark:#e2741a;
  --orange-light:#fbb05a;
  --ink:#3d3d3d;
  --muted:#555;
  --line:#d5d5d5;
  --footer:#5f5f63;
  --white:#fff;
}
*{box-sizing:border-box;margin:0;padding:0}
html,body{width:738px;height:1200px;overflow:hidden;background:var(--white)}
body{position:relative;font-family:"PT Serif",Georgia,serif;color:var(--ink)}
.abs{position:absolute}
.brand{left:60px;top:22px;font-size:26px;font-weight:700;color:var(--orange);display:flex;align-items:center;gap:7px}
.brand-dot{width:14px;height:14px;background:var(--orange);border-radius:50%}
.phone{left:498px;top:24px;font-size:8px;font-weight:700;display:flex;align-items:center;gap:5px}
.search{left:581px;top:20px;width:96px;height:18px;border:1px solid var(--line);font-size:6px;display:flex;align-items:center;justify-content:space-between;padding-left:7px;color:#555}
.search span.btn{width:18px;height:16px;border-left:1px solid var(--line);display:flex;align-items:center;justify-content:center}
.nav{left:0;top:70px;width:738px;height:20px;background:linear-gradient(var(--orange-light),var(--orange));display:flex;padding-left:61px}
.nav a{height:20px;display:flex;align-items:center;justify-content:center;font-size:7px;font-weight:700;color:var(--white);text-decoration:none;border-left:1px solid rgba(255,255,255,.55)}
.nav a:last-child{border-right:1px solid rgba(255,255,255,.55)}
.nav a.current{color:#8a4a10}
.hero{left:0;top:90px;width:738px;height:301px;background:linear-gradient(100deg,#6b4a28 0%,#a98656 30%,#d9a630 50%,#8f6a3a 70%,#4f3a22 100%)}
.hero-box{left:125px;top:160px;width:160px;height:158px;background:linear-gradient(var(--orange-light),var(--orange-dark));border:1px solid #c8651a;text-align:center;color:var(--white);font-weight:700;font-size:21px;line-height:45px;padding-top:9px;text-shadow:1px 2px 3px rgba(0,0,0,.35)}
.dots{display:flex;justify-content:center;gap:4px;margin-top:4px}
.dots i{width:6px;height:6px;border-radius:50%;background:var(--white)}
.dots i:first-child{background:#666}
.section-title{left:0;width:738px;text-align:center;font-size:13px;font-weight:700}
.section-title::after{content:"";display:block;width:76px;height:1px;background:var(--line);margin:6px auto 0}
.card{top:463px;width:146px;height:176px;border:1px solid var(--orange);text-align:center;box-shadow:0 8px 6px -6px rgba(0,0,0,.25)}
.card svg{position:absolute;left:0;top:0}
.card .pic{position:absolute;left:45px;top:14px;width:56px;height:36px;border-radius:50%}
.card h3{position:absolute;top:62px;width:100%;font-size:9px;color:var(--orange);font-weight:700}
.card p{position:absolute;top:82px;left:10px;right:10px;font-size:6.6px;line-height:9px;color:var(--muted)}
.card .more{position:absolute;top:149px;left:50px;width:46px;height:14px;background:var(--orange);color:var(--white);font-size:6.6px;font-weight:700;line-height:14px}
.about{left:60px;top:705px;width:254px;font-size:6.8px;line-height:12.8px;color:var(--muted)}
.about p{position:absolute;left:0;width:254px}
.about p::before{content:"";display:inline-block;width:7px;height:4px;background:var(--orange);border-radius:4px 0;margin-right:5px;transform:rotate(-20deg)}
.video{left:322px;top:705px;width:355px;height:214px;background:radial-gradient(ellipse at 50% 85%,#ffd36a 0%,#e67a1a 25%,#8a3410 60%,#2a1208 100%)}
.play{left:161px;top:88px;width:40px;height:26px;background:rgba(0,0,0,.75);border-radius:3px}
.bar{left:0;bottom:0;width:355px;height:16px;background:#111;display:flex;align-items:center;padding:0 6px;gap:6px}
.bar .track{flex:1;height:5px;border:1px solid #ccc}
.bar .vol{width:20px;height:6px;background:repeating-linear-gradient(90deg,#4ab0ff 0 2px,transparent 2px 3px)}
.supporters{left:127px;top:984px;width:484px;text-align:center;font-size:6.8px;line-height:12.8px;color:var(--muted)}
.partners{left:0;top:1040px;width:738px;display:flex;justify-content:center;gap:24px;font-size:12px;font-weight:700;color:var(--ink)}
.signup{left:60px;top:1087px;width:618px;height:46px;border:1px solid #bbb;display:flex;align-items:center;padding:0 6px;font-size:8px;font-weight:700;color:var(--orange)}
.signup .field{width:198px;height:20px;border:1px solid #bbb;margin:0 10px 0 8px;font-size:8px;font-weight:400;color:#999;padding:4px 7px}
.signup .field.wide{width:200px}
.signup .btn{width:92px;height:20px;background:linear-gradient(var(--orange-light),var(--orange));color:#444;font-size:10px;text-align:center;line-height:20px;margin-left:6px}
.footer{left:0;top:1162px;width:738px;height:38px;background:var(--footer);color:#eee;font-size:7px;display:flex;align-items:center;padding:0 60px 0 62px;justify-content:space-between}
</style>
</head>
<body>
<header>
  <div class="abs brand"><span class="brand-dot"></span>KW Grain</div>
  <div class="abs phone">
    <svg width="8" height="8" viewBox="0 0 8 8"><rect width="8" height="8" rx="1.5" fill="#f78f20"/><path d="M2.3 1.8l1 1-.5.6a3 3 0 0 0 1.8 1.8l.6-.5 1 1-.8.7C3.7 6 2 4.3 1.6 2.6z" fill="#fff"/></svg>
    1800 - 555 - 014
  </div>
  <div class="abs search">SEARCH<span class="btn"><svg width="9" height="9" viewBox="0 0 9 9"><circle cx="3.6" cy="3.6" r="2.6" fill="none" stroke="#f78f20" stroke-width="1.2"/><path d="M5.5 5.5L8.3 8.3" stroke="#f78f20" stroke-width="1.5"/></svg></span></div>
  <nav class="abs nav">
    <a class="current" style="width:72px">HOME</a><a style="width:80px">OUR STORY</a><a style="width:75px">FRIENDS</a><a style="width:80px">PRODUCTS</a><a style="width:127px">EVENTS &amp; GATEWAYS</a><a style="width:99px">TRADEMARKS</a><a style="width:84px">CONTACT</a>
  </nav>
</header>

<section class="abs hero" role="img" aria-label="Close-up photograph of a ripe yellow corn cob in a dry corn field"></section>
<div class="abs hero-box">LET’S GO<br>TOGETHER<div class="dots"><i></i><i></i><i></i></div></div>

<h2 class="abs section-title" style="top:416px">OUR SERVICES</h2>

<div class="abs card" style="left:60px">
  <svg width="146" height="76"><path d="M0 0H146V76H139A66 70 0 0 0 7 76H0Z" fill="#f78f20"/></svg>
  <div class="pic" role="img" aria-label="Ears of corn" style="background:radial-gradient(#f3c02c,#9cb33a 70%,transparent 72%)"></div>
  <h3>CORN</h3>
  <p>Lorem Ipsum has been the industry's standard dummy text ever since the 1500s, when an unknown printer took a galley of type and scrambled it to make a type specimen book. It has survived not only five unchanged.</p>
  <div class="more">Read More</div>
</div>
<div class="abs card" style="left:217px">
  <svg width="146" height="76"><path d="M0 0H146V76H139A66 70 0 0 0 7 76H0Z" fill="#f78f20"/></svg>
  <div class="pic" role="img" aria-label="Sack of soybeans" style="background:radial-gradient(#c9a36a,#7a5a34 70%,transparent 72%)"></div>
  <h3>SOYABEAN</h3>
  <p>Lorem Ipsum has been the industry's standard dummy text ever since the 1500s, when an unknown printer took a galley of type and scrambled it to make a type specimen book. It has survived not only five unchanged.</p>
  <div class="more">Read More</div>
</div>
<div class="abs card" style="left:374px">
  <svg width="146" height="76"><path d="M0 0H146V76H139A66 70 0 0 0 7 76H0Z" fill="#f78f20"/></svg>
  <div class="pic" role="img" aria-label="Bowls of mixed hybrid seeds" style="background:radial-gradient(#c04a3a,#6b4a3a 70%,transparent 72%)"></div>
  <h3>HYBRID SEEDS</h3>
  <p>Lorem Ipsum has been the industry's standard dummy text ever since the 1500s, when an unknown printer took a galley of type and scrambled it to make a type specimen book. It has survived not only five unchanged.</p>
  <div class="more">Read More</div>
</div>
<div class="abs card" style="left:532px">
  <svg width="146" height="76"><path d="M0 0H146V76H139A66 70 0 0 0 7 76H0Z" fill="#f78f20"/></svg>
  <div class="pic" role="img" aria-label="Scoop of small brown seeds" style="background:radial-gradient(#a0603a,#5a2e1a 70%,transparent 72%)"></div>
  <h3>SEEDS</h3>
  <p>Lorem Ipsum has been the industry's standard dummy text ever since the 1500s, when an unknown printer took a galley of type and scrambled it to make a type specimen book. It has survived not only five unchanged.</p>
  <div class="more">Read More</div>
</div>

<h2 class="abs section-title" style="top:665px">ABOUT US</h2>

<div class="abs about">
  <p style="top:0">Lorem Ipsum is not simply random text. It has roots in a piece of classical Latin literature from 45 BC, making it over 2000 years old. Richard Alwen, a Latin professor at Greyfield College in Virginia.</p>
  <p style="top:63px">Looked up one of the more obscure Latin words, consectetur, from a Lorem Ipsum passage, and going through the cites of the word in classical literature, discovered the undoubtable source.</p>
  <p style="top:126px">Lorem Ipsum comes from sections 1.10.32 and 1.10.33 of "de Finibus Bonorum et Malorum" (The Extremes of Good and Evil) by Varonius, written in 45 BC. This book is a treatise on the theory of ethics, very popular during the Renaissance. The first line of Lorem.</p>
  <p style="top:190px">And going through the cites of the word in classical literature, discovered the undoubtable source.</p>
</div>

<div class="abs video" role="img" aria-label="Video still of a sunset over a field with the Molvan name">
  <div class="abs play"><svg width="40" height="26"><path d="M16 7L26 13L16 19Z" fill="#fff"/></svg></div>
  <div class="abs bar"><div class="track"></div><div class="vol"></div><svg width="8" height="8" viewBox="0 0 8 8" fill="none" stroke="#fff"><path d="M0 3V0H3M5 0H8V3M8 5V8H5M3 8H0V5"/></svg></div>
</div>

<h2 class="abs section-title" style="top:950px">SUPPORTERS</h2>
<p class="abs supporters">Lorem Ipsum is not simply random text. It has roots in a piece of classical Latin literature from 45 BC, making it over 2000 years old. Richard Alwen, a Latin professor at Greyfield College in Virginia.m 45 BC, making it over 2000 years old. Richard Alwen, a Latin professor at Greyfield College in Virginia.</p>
<div class="abs partners"><span>Molvan</span><span>Fieldmark</span><span>Norvale Agro</span></div>

<form class="abs signup">
  NAME :<div class="field">Type your name</div>
  EMAIL :<div class="field wide">Type your email</div>
  <div class="btn">SIGNUP</div>
</form>

<footer class="abs footer">
  <span>About us &nbsp;|&nbsp; Terms &nbsp;|&nbsp; Condition &nbsp;|&nbsp; Trade</span>
  <span>© 2015 KW Grain. All rights reserved.</span>
  <span><svg width="8" height="6" viewBox="0 0 8 6"><rect width="8" height="6" fill="#eee"/><path d="M0 0L4 3.5L8 0" stroke="#5f5f63" fill="none"/></svg>&nbsp; Email : hello@kwgrain.example</span>
</footer>
</body>
</html>
```